Coral Bay Pools New website

I currently operate a swimming pool service and repair business and looking for a re design for my website as it has been over 5 years since it was designed. current site is coralbaypoolslv.com

```html
<!DOCTYPE html>
<html lang="en">
<head>
<meta charset="utf-8">
<title>Coral Bay Pools</title>
<link rel="stylesheet" href="https://fonts.googleapis.com/css2?family=Tinos:wght@400;700&family=Poppins:wght@400&family=Inter:wght@400;500;700&display=swap">
<style>
  :root{
    --blue:#1b5e97;
    --orange:#f7931e;
    --orange-btn:#fb9410;
    --ink:#2b2b2b;
    --white:#ffffff;
    --black:#000000;
    --serif:'Tinos', 'Times New Roman', serif;
    --sans:'Inter', Arial, sans-serif;
    --body:'Poppins', Arial, sans-serif;
  }
  *{margin:0;padding:0;box-sizing:border-box}
  html,body{width:1200px;height:3645px;overflow:hidden;background:var(--white)}
  .page{position:relative;width:1200px;height:3645px;overflow:hidden;font-family:var(--sans);color:var(--ink)}
  .abs{position:absolute}
  .photo{position:absolute;border-radius:6px}

  /* hero */
  .hero-bg{position:absolute;left:0;top:0}
  .brand-blob{position:absolute;left:110px;top:-30px;width:201px;height:203px;background:var(--white);border-radius:0 0 100px 100px;display:flex;align-items:center;justify-content:center;gap:8px}
  .brand-dot{width:16px;height:16px;border-radius:50%;background:var(--orange);flex:none}
  .brand-name{font-family:var(--serif);font-weight:700;font-size:21px;color:var(--blue);line-height:1.1;text-align:center;padding-top:30px}
  .nav{position:absolute;top:40px;left:375px;display:flex;gap:47px;font-family:var(--serif);font-size:16px;color:var(--white)}
  .nav a{color:var(--white);text-decoration:none}
  .nav .active{font-weight:700}
  .btn{position:absolute;display:flex;align-items:center;justify-content:center;background:var(--orange-btn);color:var(--white);font-family:var(--serif);font-weight:700;border-radius:40px;text-transform:uppercase;box-shadow:0 0 0 2px rgba(255,255,255,.25)}
  .btn-quote{left:997px;top:30px;width:126px;height:42px;font-size:15px;border:2px solid var(--white)}
  .hero-title{position:absolute;left:0;width:1200px;top:240px;text-align:center;font-family:var(--serif);font-weight:700;font-size:58px;line-height:76px;color:var(--white);text-shadow:0 3px 8px rgba(0,0,0,.55)}
  .btn-estimate{left:494px;top:415px;width:212px;height:62px;font-size:20px}
  .scroll-cue{position:absolute;left:588px;top:604px;width:24px;height:36px;border-radius:12px;background:#9a9a9a;display:flex;align-items:center;justify-content:center}

  /* about */
  .h2{font-family:var(--serif);font-weight:700;color:var(--blue);text-transform:uppercase}
  .about-title{left:110px;top:735px;font-size:38px}
  .about-brand{left:99px;top:814px;width:509px;height:339px;display:flex;align-items:center;justify-content:center;gap:18px}
  .about-brand .brand-dot{width:34px;height:34px}
  .about-brand span{font-family:var(--serif);font-weight:700;font-size:54px;color:var(--blue)}
  .about-col{left:664px;top:730px;width:424px}
  .about-text{font-family:var(--body);font-size:14px;line-height:30px;text-align:justify;color:#333}
  .about-text p+p{margin-top:30px}
  .btn-read{position:relative;margin-top:12px;width:155px;height:55px;font-size:18px}

  /* services */
  .center{left:0;width:1200px;text-align:center}
  .services-title{top:1252px;font-size:43px}
  .services-intro{left:150px;width:900px;top:1321px;font-size:15.5px;line-height:31px;text-align:center;color:#222}
  .svc-card{position:absolute;top:1412px;height:367px;border-radius:6px;overflow:hidden}
  .svc-label{position:absolute;left:50%;bottom:80px;transform-origin:left center;transform:rotate(-90deg) translateY(-50%);font-family:var(--sans);font-weight:700;font-size:21px;color:var(--white);white-space:nowrap;letter-spacing:.3px}
  .svc-bar{position:absolute;left:0;bottom:0;width:100%;height:63px;background:var(--orange-btn);display:flex;align-items:center;justify-content:space-between;padding:0 22px 0 32px;color:var(--white);font-weight:700;font-size:21px}

  /* why */
  .why-band{left:0;top:1875px;width:1200px;height:311px;background:var(--orange)}
  .why-title{top:1935px;font-size:43px;color:var(--white)}
  .why-text{left:180px;width:840px;top:2001px;font-size:15.5px;line-height:31px;text-align:center;color:var(--white)}
  .why-photo{top:2096px;height:283px;border:3px solid var(--white);border-radius:8px}
  .arrow-btn{position:absolute;top:2247px;width:38px;height:38px}

  /* projects */
  .projects-title{top:2445px;font-size:43px}
  .btn-more{left:524px;top:3048px;width:154px;height:55px;font-size:18px}

  /* footer */
  .footer-bg{position:absolute;left:0;top:0}
  .footer-brand{left:110px;top:3311px;width:293px;height:198px;display:flex;align-items:center;justify-content:center;gap:12px}
  .footer-brand .brand-dot{width:22px;height:22px}
  .footer-brand span{font-family:var(--serif);font-weight:700;font-size:32px;color:var(--white)}
  .f-head{position:absolute;top:3310px;font-family:var(--serif);font-size:20px;font-weight:400;color:var(--white);text-transform:uppercase}
  .f-list{position:absolute;top:3350px;list-style:none;color:var(--white);font-size:15.5px}
  .f-list li{height:34px;display:flex;align-items:center;gap:10px}
  .contact-row{position:absolute;left:819px;display:flex;align-items:center;gap:12px;color:var(--white);font-size:15.5px;line-height:27px}
  .c-ico{width:32px;height:32px;border-radius:50%;background:var(--white);display:flex;align-items:center;justify-content:center;flex:none}
  .f-rule{left:110px;top:3557px;width:978px;height:1px;background:#444}
  .copyright{top:3590px;font-size:15.5px;font-weight:500;color:var(--white)}
</style>
</head>
<body>
<div class="page">

  <!-- hero -->
  <svg class="hero-bg" width="1200" height="660" viewBox="0 0 1200 660" role="img" aria-label="Evening view of a luxury resort courtyard pool lit by lanterns">
    <defs>
      <linearGradient id="heroGrad" x1="0" y1="0" x2="0" y2="1">
        <stop offset="0" stop-color="#1d2a3e"/>
        <stop offset=".35" stop-color="#4a4a6a"/>
        <stop offset=".65" stop-color="#6b4a32"/>
        <stop offset="1" stop-color="#1f4a4a"/>
      </linearGradient>
      <radialGradient id="heroGlow" cx=".5" cy=".3" r=".5">
        <stop offset="0" stop-color="#8a8fd0" stop-opacity=".45"/>
        <stop offset="1" stop-color="#8a8fd0" stop-opacity="0"/>
      </radialGradient>
    </defs>
    <path d="M0 0H1200V545Q600 715 0 545Z" fill="url(#heroGrad)"/>
    <path d="M0 0H1200V545Q600 715 0 545Z" fill="url(#heroGlow)"/>
    <circle cx="600" cy="622" r="36" fill="#ffffff"/>
  </svg>
  <div class="scroll-cue"><svg width="12" height="22" viewBox="0 0 12 22"><path d="M6 2V19M1 14L6 19L11 14" stroke="#fff" stroke-width="1.8" fill="none"/></svg></div>

  <div class="brand-blob"><span class="brand-name">Coral Bay<br>Pools</span></div>
  <nav class="nav">
    <a class="active">HOME</a><a>ABOUT</a><a>SERVICES</a><a>FREE ESTIMATE</a><a>CONTACT</a>
  </nav>
  <div class="btn btn-quote">Get a Quote</div>
  <h1 class="hero-title">LUXURY POOLS DESIGNED<br>FOR LIFE IN LAS VEGAS</h1>
  <div class="btn btn-estimate">Free Estimate</div>

  <!-- about -->
  <h2 class="abs h2 about-title">About Coral Bay</h2>
  <div class="abs about-brand"><span class="brand-dot"></span><span>Coral Bay Pools</span></div>
  <div class="abs about-col">
    <div class="about-text">
      <p>My name is Marcus and I’m the owner of Coral Bay pools. I recently started this business in 2016 to provide Las Vegas with excellent, reliable pool service. Just because we are a new company that doesn’t mean we lack experience. I’ve been in the pool industry for seven years and counting and have managed everything from your backyard pool to olympic sized pools with five plus years managing casino properties as well.</p>
      <p>In that time i’ve worked on all kinds of pumps, filters, lights, heaters, chlorinators and any other equipment you have on your pool.</p>
    </div>
    <div class="btn btn-read">Read More</div>
  </div>

  <!-- services -->
  <h2 class="abs h2 center services-title">Our Services</h2>
  <p class="abs services-intro">uis aute irure dolor in reprehenderit in voluptate velit esse cillum dolore eu fugiat nulla pariatur. Excepteur sint occaecat cupidatat non proident, sunt in culpa qui officia deserunt mollit anim id est laborum.</p>

  <div class="svc-card" style="left:112px;width:151px;background:linear-gradient(160deg,#1a4f8f,#0f3a72 60%,#2a6ab0)" role="img" aria-label="Top view of blue pool water with tiled floor">
    <span class="svc-label">POOL SERVICES</span>
  </div>
  <div class="svc-card" style="left:282px;width:151px;background:linear-gradient(180deg,#e4dbd0 0%,#c9bfb2 40%,#6fa7b6 58%,#8e8f8e 75%,#8c8a88 100%)" role="img" aria-label="Covered terrace overlooking a commercial pool">
    <span class="svc-label">COMMERCIAL POOL</span>
  </div>
  <div class="svc-card" style="left:450px;width:638px;background:linear-gradient(180deg,#5f7f4a 0%,#7d9a5c 22%,#9aa0a0 42%,#2f8fd0 62%,#1f6fb8 82%)" role="img" aria-label="Freeform backyard pool with paver deck, rock waterfall and landscaping">
    <div class="svc-bar"><span>RESIDENTIAL POOL SERVICES</span>
      <svg width="26" height="18" viewBox="0 0 26 18"><path d="M1 9H24M16 1L24 9L16 17" stroke="#fff" stroke-width="2.4" fill="none"/></svg>
    </div>
  </div>

  <!-- why choose us -->
  <div class="abs why-band"></div>
  <h2 class="abs h2 center why-title">Why Choose Us?</h2>
  <p class="abs why-text">Our full-service pool company proudly serves the entire Las Vegas valley, and we’re certified by the Desert Valley Health District to maintain the highest level of pool safety.</p>
  <div class="photo why-photo" style="left:122px;width:469px;background:linear-gradient(180deg,#8e9aa6,#5e6a74 45%,#36434c 70%,#4f6670)" role="img" aria-label="Modern glass house at dusk with a reflecting pool"></div>
  <div class="photo why-photo" style="left:608px;width:470px;background:linear-gradient(180deg,#7f9ab3,#6e7a80 40%,#3f4a4c 65%,#274246)" role="img" aria-label="Stone villa with an evening-lit swimming pool"></div>
  <svg class="arrow-btn" style="left:39px" viewBox="0 0 38 38"><circle cx="19" cy="19" r="17" fill="#fff" stroke="#555" stroke-width="1.6"/><path d="M27 19H11M17 13L11 19L17 25" stroke="#555" stroke-width="1.8" fill="none"/></svg>
  <svg class="arrow-btn" style="left:1117px" viewBox="0 0 38 38"><circle cx="19" cy="19" r="17" fill="#fff" stroke="#555" stroke-width="1.6"/><path d="M11 19H27M21 13L27 19L21 25" stroke="#555" stroke-width="1.8" fill="none"/></svg>

  <!-- past projects -->
  <h2 class="abs h2 center projects-title">Past Projects</h2>
  <div class="photo" style="left:112px;top:2540px;width:271px;height:260px;background:linear-gradient(180deg,#5d7fb0,#8a7860 40%,#1d4fa0 70%,#123a80)" role="img" aria-label="Two-storey home with a blue-lit pool at dusk"></div>
  <div class="photo" style="left:112px;top:2809px;width:271px;height:185px;background:linear-gradient(180deg,#6d8f4f,#c9c2b0 45%,#30b0d8 75%,#1a90c0)" role="img" aria-label="Backyard pool beside a white house and trees"></div>
  <div class="photo" style="left:392px;top:2540px;width:398px;height:453px;background:linear-gradient(160deg,#7ea8d0,#5aa0d8 35%,#3fb7e0 55%,#a9b8c8 80%)" role="img" aria-label="Pool builder reviewing plans beside a pool"></div>
  <div class="photo" style="left:798px;top:2540px;width:290px;height:187px;background:linear-gradient(180deg,#b7a7b0,#e4ddd6 40%,#3c8ea8 70%,#6a7a80)" role="img" aria-label="Modern villa with an infinity pool at sunset"></div>
  <div class="photo" style="left:798px;top:2735px;width:290px;height:259px;background:linear-gradient(180deg,#4c4c48,#7c786c 40%,#d8d2c4 70%,#c9c2b4)" role="img" aria-label="Worker scrubbing a pool deck with a brush"></div>
  <div class="btn btn-more">View More</div>

  <!-- footer -->
  <svg class="footer-bg" width="1200" height="3645" viewBox="0 0 1200 3645" aria-hidden="true"><path d="M0 3269Q600 3085 1200 3269V3645H0Z" fill="#000"/></svg>
  <div class="abs footer-brand"><span class="brand-dot"></span><span>Coral Bay Pools</span></div>

  <h3 class="f-head" style="left:439px">Quick Links</h3>
  <ul class="f-list" style="left:439px">
    <li><svg width="14" height="12" viewBox="0 0 14 12"><path d="M1 6H12M7 1L12 6L7 11" stroke="#fff" stroke-width="2.2" fill="none"/></svg>Home</li>
    <li><svg width="14" height="12" viewBox="0 0 14 12"><path d="M1 6H12M7 1L12 6L7 11" stroke="#fff" stroke-width="2.2" fill="none"/></svg>About</li>
    <li><svg width="14" height="12" viewBox="0 0 14 12"><path d="M1 6H12M7 1L12 6L7 11" stroke="#fff" stroke-width="2.2" fill="none"/></svg>Services</li>
    <li><svg width="14" height="12" viewBox="0 0 14 12"><path d="M1 6H12M7 1L12 6L7 11" stroke="#fff" stroke-width="2.2" fill="none"/></svg>Free Estimate</li>
    <li><svg width="14" height="12" viewBox="0 0 14 12"><path d="M1 6H12M7 1L12 6L7 11" stroke="#fff" stroke-width="2.2" fill="none"/></svg>Contact Us</li>
  </ul>

  <h3 class="f-head" style="left:628px">Help Links</h3>
  <ul class="f-list" style="left:628px">
    <li><svg width="14" height="12" viewBox="0 0 14 12"><path d="M1 6H12M7 1L12 6L7 11" stroke="#fff" stroke-width="2.2" fill="none"/></svg>FAQ</li>
    <li><svg width="14" height="12" viewBox="0 0 14 12"><path d="M1 6H12M7 1L12 6L7 11" stroke="#fff" stroke-width="2.2" fill="none"/></svg>Terms of use</li>
    <li><svg width="14" height="12" viewBox="0 0 14 12"><path d="M1 6H12M7 1L12 6L7 11" stroke="#fff" stroke-width="2.2" fill="none"/></svg>Privacy Policy</li>
    <li><svg width="14" height="12" viewBox="0 0 14 12"><path d="M1 6H12M7 1L12 6L7 11" stroke="#fff" stroke-width="2.2" fill="none"/></svg>Support Links</li>
    <li><svg width="14" height="12" viewBox="0 0 14 12"><path d="M1 6H12M7 1L12 6L7 11" stroke="#fff" stroke-width="2.2" fill="none"/></svg>Conditions</li>
  </ul>

  <h3 class="f-head" style="left:819px">Contact Us</h3>
  <div class="contact-row" style="top:3348px">
    <span class="c-ico"><svg width="14" height="18" viewBox="0 0 14 18"><path d="M7 1C3.7 1 1 3.6 1 6.9C1 11 7 17 7 17S13 11 13 6.9C13 3.6 10.3 1 7 1Z" fill="#000"/><circle cx="7" cy="7" r="2.2" fill="#fff"/></svg></span>
    <span>Coral Bay<br>Nevada’s</span>
  </div>
  <div class="contact-row" style="top:3419px">
    <span class="c-ico"><svg width="16" height="16" viewBox="0 0 16 16"><path d="M3 1L6 1L7 5L5 6.5C6 8.8 7.2 10 9.5 11L11 9L15 10L15 13C15 14 14 15 13 15C6.4 15 1 9.6 1 3C1 2 2 1 3 1Z" fill="#000"/></svg></span>
    <span>(702) 555-0148</span>
  </div>
  <div class="contact-row" style="top:3471px">
    <span class="c-ico"><svg width="16" height="12" viewBox="0 0 16 12"><rect x="0" y="0" width="16" height="12" rx="2" fill="#000"/><path d="M1 1L8 7L15 1" stroke="#fff" stroke-width="1.4" fill="none"/></svg></span>
    <span>poolsolutions@coralbaypoolslv.com</span>
  </div>

  <div class="abs f-rule"></div>
  <p class="abs center copyright">Copyrights@2026.Coral Bay.All Rights Reserved</p>
</div>
</body>
</html>
```